Creative, fresh business card design for Ripplecraft Facades

We need a fresh, creative business card design for Ripplecraft Facades. We are the manufacturer of Ripplecraft Facades in Australia. Wall panels are 2400 x 1200mm panels made from MDF and feature 3D patterns on the face of the panel. The colours to be used are green, silver/grey and white RGB
Red 187
Green 207
Blue 65.

An idea is to possibly use a watermark of one of our designs as a background (like on the "Grids" design on the left hand side of page 2 of our brochure).

Target Market(s)

Interior designers, architects, builders and home renovators

Industry/Entity Type

Business

Contact Information for Business Card

Details to go on the card are:
Our logo (attached),
Slogan: "Decorative panels for interiors and exteriors",
Contact name,
Position,
Mobile phone number,
Business address,
Business phone,
Business fax,
Website and
Email address.

I have attached a few images of our panels and our brochure for reference.

The colours of the business card should feature our logo colours which are: RGB
Red 187
Green 207
Blue 65

Requirements
Must have
• Very modern fonts and design. Some of the designs shown especially the "Prisms" design which is a popular design.
Nice to have
• Creative but simple design. Very contemporary.
Should not have
• Anything ornate or old fashioned.

```html
<!DOCTYPE html>
<html lang="en">
<head>
<meta charset="utf-8">
<title>Ripplecraft Facades – Business Card</title>
<link rel="stylesheet" href="https://fonts.googleapis.com/css2?family=Open+Sans:wght@400;600&family=Courier+Prime&display=swap">
<style>
  :root {
    --page-bg: #e7e6e3;
    --panel-white: #f6f6f4;
    --panel-shade: #e2e2df;
    --brand-green: #bbcf41;
    --brand-green-deep: #a3b733;
    --silver: #b9bbbd;
    --brand-grey: #6f7072;
    --slogan-ink: #4a4a4a;
    --contact-ink: #2b2d2f;
  }
  * { margin: 0; padding: 0; box-sizing: border-box; }
  html, body {
    width: 1200px;
    height: 1000px;
    overflow: hidden;
    background: var(--page-bg);
  }
  .business-card {
    position: absolute;
    left: 150px;
    top: 245px;
    width: 900px;
    height: 505px;
    overflow: hidden;
    box-shadow: 0 10px 28px rgba(0, 0, 0, 0.28);
  }
  .card-artwork {
    position: absolute;
    inset: 0;
    width: 100%;
    height: 100%;
  }
  .brand-block {
    position: absolute;
    left: 0;
    right: 0;
    top: 22px;
    display: flex;
    flex-direction: column;
    align-items: center;
  }
  .brand-name {
    display: flex;
    align-items: center;
    gap: 14px;
    font-family: "Open Sans", sans-serif;
    font-weight: 600;
    font-size: 40px;
    color: var(--brand-grey);
    letter-spacing: 0.5px;
    line-height: 1;
  }
  .brand-square {
    width: 40px;
    height: 40px;
    background: var(--brand-green);
  }
  .brand-slogan {
    margin-top: 26px;
    font-family: "Courier Prime", monospace;
    font-size: 21px;
    line-height: 1.25;
    color: var(--slogan-ink);
    text-align: left;
    padding-left: 12px;
  }
  .contact-person {
    position: absolute;
    left: 27px;
    top: 168px;
    font-family: "Open Sans", sans-serif;
    color: var(--brand-grey);
  }
  .person-name {
    font-size: 24px;
    font-weight: 600;
    line-height: 32px;
  }
  .person-role {
    font-size: 17px;
    font-weight: 400;
    line-height: 26px;
  }
  .contact-list {
    position: absolute;
    left: 27px;
    top: 322px;
    list-style: none;
    font-family: "Open Sans", sans-serif;
    font-size: 18px;
    line-height: 28px;
    color: var(--contact-ink);
  }
</style>
</head>
<body>
  <article class="business-card">
    <svg class="card-artwork" viewBox="0 0 900 505" xmlns="http://www.w3.org/2000/svg">
      <defs>
        <linearGradient id="panel-texture" x1="0" y1="0" x2="1" y2="1">
          <stop offset="0" stop-color="var(--panel-white)"/>
          <stop offset="0.5" stop-color="var(--panel-shade)"/>
          <stop offset="1" stop-color="var(--panel-white)"/>
        </linearGradient>
        <linearGradient id="wave-fill" x1="0" y1="0" x2="0" y2="1">
          <stop offset="0" stop-color="var(--brand-green)"/>
          <stop offset="1" stop-color="var(--brand-green-deep)"/>
        </linearGradient>
      </defs>
      <rect class="panel-surface" width="900" height="505" fill="url(#panel-texture)"
            role="img" aria-label="White sculpted wall panel with flowing ripple relief"/>
      <path class="silver-edge" fill="var(--silver)"
            d="M0 290 C60 266 110 244 174 246 C300 250 420 332 560 344 C640 350 700 348 760 322 C820 296 860 268 900 262 L900 505 L0 505 Z"/>
      <path class="green-wave" fill="url(#wave-fill)"
            role="img" aria-label="Green rippled wall panel relief beneath a sweeping curve"
            d="M0 298 C60 274 110 252 174 254 C300 258 420 340 560 352 C640 358 700 356 760 330 C820 304 860 276 900 270 L900 505 L0 505 Z"/>
    </svg>

    <header class="brand-block">
      <div class="brand-name"><span class="brand-square"></span>Ripplecraft Facades</div>
      <p class="brand-slogan">Decorative panels for<br>interiors and exteriors</p>
    </header>

    <div class="contact-person">
      <p class="person-name">Daniel Morrow</p>
      <p class="person-role">Sales Manager</p>
    </div>

    <ul class="contact-list">
      <li>Mobile: 0400 555 218</li>
      <li>Telephone: 02 5550 1840</li>
      <li>Business fax: 02 5550 1841</li>
      <li>14 Harbourline Road, Kellmont NSW 2170</li>
      <li>www.ripplecraftfacades.com.au</li>
      <li>sales@ripplecraftfacades.com.au</li>
    </ul>
  </article>
</body>
</html>
```